WordPress Design for both website and landing page for an expert

I need a clean and stylish design for my new website. I work as an expert (see attached file WHY HOW WHAT), my product is expert opinion (reports) for company evaluations You can use all of the attached pictures colored or black / white. The person is me, you can add other pictures, if you want. The design should be clean and stylish, so you could use white, black, gray, silver and / or one additional color. I have added an idea about my website, see attached file CONCEPT WEBSITE If you have any more information, please do not hesitate to contact us 'Hesitate to ask me ...

```html
<!DOCTYPE html>
<html lang="en">
<head>
<meta charset="utf-8">
<title>Contact – Lukas Brenner</title>
<link rel="stylesheet" href="https://fonts.googleapis.com/css2?family=Montserrat:wght@400;500;600&display=swap">
<style>
  :root {
    --ink: #1f2226;
    --ink-soft: #3a3f45;
    --muted: #7d858d;
    --accent: #8fa0a4;
    --field: #eff2f5;
    --footer: #eef1f4;
    --white: #ffffff;
    --line: #c9ced3;
    --sky: #3f96d6;
    --water: #2b6f9c;
    --map: #e9e9e9;
  }
  * { box-sizing: border-box; margin: 0; padding: 0; }
  html, body { width: 1080px; height: 1200px; overflow: hidden; }
  body {
    position: relative;
    background: var(--white);
    color: var(--ink);
    font-family: "Montserrat", Arial, sans-serif;
  }

  .site-header { position: absolute; top: 0; left: 0; width: 1080px; height: 120px; }
  .brand {
    position: absolute; left: 61px; top: 46px;
    display: flex; align-items: center; gap: 10px;
    font-size: 17px; font-weight: 400; letter-spacing: 3px;
    color: var(--ink); text-transform: uppercase;
  }
  .brand-mark { width: 12px; height: 12px; background: var(--ink); }
  .main-nav { position: absolute; top: 54px; left: 0; }
  .main-nav a {
    position: absolute; white-space: nowrap;
    font-size: 11px; font-weight: 500; letter-spacing: 1.6px;
    color: var(--ink); text-decoration: none; text-transform: uppercase;
  }
  .main-nav a.is-active { color: var(--accent); }

  .hero {
    position: absolute; left: 123px; top: 177px; width: 833px; height: 339px;
    display: flex;
  }
  .hero-photo {
    width: 417px; height: 100%;
    background: linear-gradient(180deg, var(--sky) 0%, #6fb2e0 45%, #4d7f9e 62%, var(--water) 80%, #1f4c6a 100%);
  }
  .hero-map { width: 416px; height: 100%; background: var(--map); }
  .hero-title {
    position: absolute; left: 0; top: 124px; width: 833px;
    text-align: center;
    font-size: 38px; font-weight: 500; letter-spacing: 3px; line-height: 44px;
    color: var(--ink-soft); text-transform: uppercase;
  }

  .contact-details { position: absolute; top: 582px; left: 0; width: 1080px; }
  .detail {
    position: absolute; width: 200px; margin-left: -100px;
    text-align: center;
  }
  .detail svg { display: block; margin: 0 auto 12px; }
  .detail-main { font-size: 15px; color: var(--muted); letter-spacing: .3px; line-height: 20px; }
  .detail-sub { font-size: 10.5px; color: var(--muted); line-height: 19px; }
  .detail-address { font-size: 11.5px; color: var(--muted); line-height: 19px; letter-spacing: .3px; }

  .help-title {
    position: absolute; top: 738px; left: 0; width: 1080px;
    text-align: center; font-size: 24px; font-weight: 500; line-height: 31px;
    color: var(--ink);
  }

  .contact-form { position: absolute; left: 0; top: 0; }
  .field {
    position: absolute; background: var(--field); border-radius: 2px;
    font-size: 10px; letter-spacing: 1px; color: var(--muted);
    text-transform: uppercase; padding: 0 19px; line-height: 35px;
  }
  .field-message { line-height: 1; padding-top: 12px; }
  .submit-button {
    position: absolute; left: 474px; top: 1040px; width: 131px; height: 36px;
    border: 2px solid var(--line); border-radius: 18px; background: var(--white);
    font-family: "Montserrat", Arial, sans-serif;
    font-size: 11px; font-weight: 600; letter-spacing: 1.5px; color: var(--ink);
    text-transform: uppercase;
  }

  .site-footer {
    position: absolute; left: 0; top: 1138px; width: 1080px; height: 62px;
    background: var(--footer);
  }
  .copyright {
    position: absolute; left: 123px; top: 25px;
    font-size: 10px; color: var(--muted); letter-spacing: .3px;
  }
  .social-links { position: absolute; top: 12px; left: 0; }
  .social-link {
    position: absolute; width: 37px; height: 37px; border-radius: 50%;
    background: var(--white);
  }
</style>
</head>
<body>
  <header class="site-header">
    <div class="brand"><span class="brand-mark"></span>Lukas Brenner</div>
    <nav class="main-nav">
      <a style="left:537px">Home</a>
      <a style="left:609px">About</a>
      <a style="left:690px">What I do</a>
      <a style="left:798px">Why / How I do</a>
      <a class="is-active" style="left:950px">Contact</a>
    </nav>
  </header>

  <section class="hero">
    <div class="hero-photo" role="img" aria-label="City skyline with a tall tower beside a river at dusk"></div>
    <div class="hero-map" role="img" aria-label="Grey road map of Germany and neighbouring countries"></div>
    <h1 class="hero-title">Contact<br>Me</h1>
  </section>

  <section class="contact-details">
    <div class="detail" style="left:339px; top:4px">
      <svg width="22" height="22" viewBox="0 0 24 24" fill="none" stroke="#5a6067" stroke-width="1.4" stroke-linejoin="round"><path d="M5 3h4l2 5-2.5 1.5a11 11 0 0 0 6 6L16 13l5 2v4a2 2 0 0 1-2 2A17 17 0 0 1 3 5a2 2 0 0 1 2-2z"/></svg>
      <div class="detail-main">+1-202-555-0178</div>
      <div class="detail-sub">Call Us Today!</div>
    </div>
    <div class="detail" style="left:539px; top:0">
      <svg width="22" height="30" viewBox="0 0 22 30" fill="none" stroke="#5a6067" stroke-width="1.4"><path d="M11 28C5 19 2 14 2 10a9 9 0 0 1 18 0c0 4-3 9-9 18z"/><circle cx="11" cy="10" r="2.6"/></svg>
      <div class="detail-address">48 Harbor Lane<br>Fairview, MD 20870<br>Germany</div>
    </div>
    <div class="detail" style="left:740px; top:6px">
      <svg width="24" height="18" viewBox="0 0 24 18" fill="none" stroke="#5a6067" stroke-width="1.4"><rect x="1" y="1" width="22" height="16"/><path d="M1 1l11 9 11-9"/></svg>
      <div class="detail-main">hello@brennerexpert.com</div>
      <div class="detail-sub">Inquire Now!</div>
    </div>
  </section>

  <h2 class="help-title">How can I help<br>you today!</h2>

  <form class="contact-form">
    <div class="field" style="left:254px; top:833px; width:201px; height:35px">Enter your name</div>
    <div class="field" style="left:470px; top:833px; width:201px; height:35px">Email</div>
    <div class="field" style="left:686px; top:833px; width:139px; height:35px">Phone</div>
    <div class="field field-message" style="left:254px; top:886px; width:571px; height:114px">Message</div>
    <button class="submit-button" type="button">Submit</button>
  </form>

  <footer class="site-footer">
    <p class="copyright">Copyright © 2018 Lukas Brenner. All Rights Reserved</p>
    <div class="social-links">
      <span class="social-link" style="left:825px"></span>
      <span class="social-link" style="left:871px"></span>
      <span class="social-link" style="left:919px"></span>
    </div>
  </footer>
</body>
</html>
```